Briloran Clear Springs needs a new business card design (we produce and sell pure bottled water)

We need a clean modern design for our new business cards, We have an existing logo which ultimately cannot be changed, however it could be slighty improved and the colours adjusted. We have this existing logo on all of our bottles, vehicles etc.

Our company slogan is "Clear from source to sip".
Along with our relevant company information
(Address, phone, website email etc) we will only be using names and not putting position titles for flexibilty.

We are looking for a clean, minimalist modern design.

You can view our website (if need of an update also!) to see our business.

Industry/Entity Type

Business

Contact Information for Business Card

Staff Name : XXXXXX XXXXXX
Address : 9/41 Tavenor St
Halden Rise QLD 4172
Staff Mobile Number : 04XX XXX XXX
Office Phone Number : 07 3918 2457
Staff Email Address : XXXX@brilorancleargo.com.au
Website : www.brilorancleargo.com.au

Font styles to use
Sans Serif

Colors
cee9f5
33a6d7
0492cd
0455a3
3276b5
85abd2
cedeed

Requirements
Must have
• The ability to edit and change the staff members details as we will need to edit for each respective staff member (7 in total)

```html
<!DOCTYPE html>
<html lang="en">
<head>
<meta charset="utf-8">
<title>Briloran Clear Springs – Business Card</title>
<link href="https://fonts.googleapis.com/css2?family=Open+Sans:wght@400;600;700&display=swap" rel="stylesheet">
<style>
  :root {
    --stage: #e8ecef;
    --card-white: #ffffff;
    --card-black: #0b0b0c;
    --brand-blue: #0492cd;
    --deep-blue: #0455a3;
    --mid-blue: #3276b5;
    --sky-blue: #33a6d7;
    --pale-blue: #cee9f5;
    --mist-blue: #cedeed;
    --ink: #3a3a3a;
  }
  * { box-sizing: border-box; margin: 0; padding: 0; }
  html, body {
    width: 1200px; height: 900px; overflow: hidden;
    background: var(--stage);
    font-family: "Open Sans", Arial, sans-serif;
  }
  .stage {
    width: 1200px; height: 900px;
    display: flex; align-items: center; justify-content: center; gap: 40px;
  }
  .card {
    width: 540px; height: 330px;
    position: relative;
    box-shadow: 0 6px 18px rgba(0,0,0,0.18);
  }

  /* Back side */
  .card--back {
    background: var(--card-black);
    display: flex; align-items: center; justify-content: center;
  }
  .brand-mark {
    display: flex; align-items: center; gap: 14px;
  }
  .brand-mark__dot {
    width: 22px; height: 22px; border-radius: 50%;
    background: var(--brand-blue);
  }
  .brand-mark__name {
    color: var(--brand-blue);
    font-weight: 700; font-size: 30px; letter-spacing: 0.5px;
    text-transform: uppercase; line-height: 1.1;
  }

  /* Front side */
  .card--front {
    background: linear-gradient(135deg, #ffffff 0%, #ffffff 55%, #f3f6f8 100%);
  }
  .product-photo {
    position: absolute; left: 40px; top: 40px;
    width: 170px; height: 250px;
    background: radial-gradient(ellipse at 45% 40%, var(--pale-blue) 0%, var(--sky-blue) 55%, var(--mid-blue) 100%);
    border-radius: 6px;
  }
  .contact {
    position: absolute; left: 250px; top: 42px; right: 20px;
    color: var(--ink);
  }
  .contact__name {
    color: var(--brand-blue);
    font-weight: 600; font-size: 17px;
    margin-bottom: 18px;
  }
  .contact__address {
    font-size: 13px; line-height: 1.35;
    margin-bottom: 16px;
  }
  .contact__list { list-style: none; }
  .contact__item {
    display: flex; align-items: center; gap: 8px;
    font-size: 13px; line-height: 1.5;
  }
  .contact__icon { width: 11px; height: 11px; flex: none; fill: var(--mid-blue); }
  .slogan {
    margin-top: 18px;
    color: var(--deep-blue);
    font-weight: 700; font-size: 14px; letter-spacing: 0.3px;
    text-transform: uppercase;
  }
</style>
</head>
<body>
<main class="stage">

  <section class="card card--back" aria-label="Card back">
    <div class="brand-mark">
      <span class="brand-mark__dot"></span>
      <span class="brand-mark__name">Briloran<br>Clear Springs</span>
    </div>
  </section>

  <section class="card card--front" aria-label="Card front">
    <div class="product-photo" role="img" aria-label="Photo of a large blue water cooler bottle"></div>

    <div class="contact">
      <p class="contact__name">Marella Dunstan</p>
      <p class="contact__address">9/41 Tavenor St<br>Halden Rise QLD 4172</p>
      <ul class="contact__list">
        <li class="contact__item">
          <svg class="contact__icon" viewBox="0 0 12 12"><path d="M1 4c0-2 2-3 5-3s5 1 5 3l-2 1-1-2H4L3 5 1 4zM2 6h8v5H2z"/></svg>
          0400 582 913
        </li>
        <li class="contact__item">
          <svg class="contact__icon" viewBox="0 0 12 12"><path d="M3 0h6v12H3zM4 1.5v8h4v-8z"/></svg>
          07 3918 2457
        </li>
        <li class="contact__item">
          <svg class="contact__icon" viewBox="0 0 12 12"><path d="M0 2h12v8H0zM1 3l5 4 5-4v-.2H1z"/></svg>
          info@brilorancleargo.com.au
        </li>
        <li class="contact__item">
          <svg class="contact__icon" viewBox="0 0 12 12"><circle cx="6" cy="6" r="5.5"/></svg>
          www.brilorancleargo.com.au
        </li>
      </ul>
      <p class="slogan">Clear from source to sip</p>
    </div>
  </section>

</main>
</body>
</html>
```